BOLD & MINIMALIST DESIGN NEEDED

We want a very bold but minimalistic business card design that is impactful and utilizes both sides of the business card. Our current logo is included for your use.

We want bold fonts and good use of negative space. We don't want the logo to overpower the design.

Target Market(s)

Professionals who are building new commercial buildings.

Industry/Entity Type

Construction

Contact Information for Business Card

Name, Title, email, office phone, cell phone, website

Font styles to use
Serif
Sans Serif

Requirements
Must have
• Bold design!

```html
<!DOCTYPE html>
<html lang="en">
<head>
<meta charset="utf-8">
<title>Summitcrest Build Co. — Business Card</title>
<link rel="stylesheet" href="https://fonts.googleapis.com/css2?family=Montserrat:wght@400;500;700;800&display=swap">
<style>
  :root {
    --stage: #3a3b3d;
    --ink: #1c1c1c;
    --paper: #ffffff;
    --accent: #7cc242;
    --muted: #4a4a4a;
    --light: #f2f2f2;
  }
  html, body {
    margin: 0;
    padding: 0;
    width: 1200px;
    height: 1200px;
    overflow: hidden;
    background: var(--stage);
    font-family: "Montserrat", Arial, sans-serif;
  }
  .canvas {
    position: relative;
    width: 1200px;
    height: 1200px;
  }
  .card {
    position: absolute;
    left: 170px;
    width: 860px;
    height: 491px;
    border-radius: 34px;
    overflow: hidden;
    box-shadow: 0 0 0 3px var(--accent);
  }
  .card--front { top: 70px; background: var(--paper); }
  .card--back  { top: 639px; background: var(--ink); }

  .card__art {
    position: absolute;
    inset: 0;
    width: 100%;
    height: 100%;
  }

  .brand {
    position: absolute;
    display: flex;
    align-items: center;
    gap: 14px;
    font-weight: 800;
    letter-spacing: 0.02em;
    text-transform: uppercase;
    white-space: nowrap;
  }
  .brand__mark {
    background: var(--accent);
    flex: none;
  }
  .card--front .brand {
    left: 120px;
    top: 118px;
    font-size: 34px;
    color: var(--ink);
  }
  .card--front .brand__mark { width: 30px; height: 30px; }

  .card--back .brand {
    left: 0;
    right: 0;
    top: 0;
    bottom: 0;
    justify-content: center;
    font-size: 48px;
    color: var(--paper);
  }
  .card--back .brand__mark { width: 42px; height: 42px; }

  .person {
    position: absolute;
    left: 70px;
    top: 372px;
    color: var(--paper);
  }
  .person__name {
    margin: 0;
    font-size: 36px;
    font-weight: 500;
    color: var(--accent);
    letter-spacing: 0.01em;
    line-height: 1;
  }
  .person__title {
    margin: 6px 0 10px;
    font-size: 24px;
    font-weight: 400;
    line-height: 1;
  }

  .contact {
    list-style: none;
    margin: 0;
    padding: 0;
  }
  .contact__item {
    display: flex;
    align-items: center;
    gap: 12px;
    font-size: 20px;
    font-weight: 400;
    color: var(--paper);
    line-height: 1;
  }
  .contact--office {
    position: absolute;
    left: 540px;
    top: 262px;
    display: flex;
    flex-direction: column;
    gap: 18px;
  }
  .contact__icon {
    width: 22px;
    height: 22px;
    flex: none;
  }
  .divider {
    position: absolute;
    left: 480px;
    top: 300px;
    width: 1px;
    height: 130px;
    background: var(--muted);
  }
</style>
</head>
<body>
<main class="canvas">

  <section class="card card--front" aria-label="Card front">
    <svg class="card__art" viewBox="0 0 860 491" preserveAspectRatio="none" aria-hidden="true">
      <line x1="0" y1="352" x2="860" y2="170" stroke="var(--accent)" stroke-width="9"/>
      <polygon points="0,368 860,186 860,491 0,491" fill="var(--ink)"/>
    </svg>

    <div class="brand">
      <span class="brand__mark"></span>
      <span class="brand__name">Summitcrest Build Co.</span>
    </div>

    <div class="person">
      <h1 class="person__name">FULL NAME</h1>
      <p class="person__title">TITLE</p>
      <ul class="contact">
        <li class="contact__item">
          <svg class="contact__icon" viewBox="0 0 24 24" aria-hidden="true">
            <rect x="2" y="5" width="20" height="14" fill="var(--accent)"/>
            <polyline points="2,5 12,13 22,5" fill="none" stroke="var(--ink)" stroke-width="2"/>
          </svg>
          email@company.com
        </li>
      </ul>
    </div>

    <span class="divider"></span>

    <ul class="contact contact--office">
      <li class="contact__item">
        <svg class="contact__icon" viewBox="0 0 24 24" aria-hidden="true">
          <rect x="6" y="2" width="12" height="20" rx="2" fill="none" stroke="var(--accent)" stroke-width="2"/>
          <line x1="10" y1="18" x2="14" y2="18" stroke="var(--accent)" stroke-width="2"/>
        </svg>
        (000) 000 0000
      </li>
      <li class="contact__item">
        <svg class="contact__icon" viewBox="0 0 24 24" aria-hidden="true">
          <path d="M6.6 10.8a15 15 0 0 0 6.6 6.6l2.2-2.2a1 1 0 0 1 1-.25 11.4 11.4 0 0 0 3.6.57 1 1 0 0 1 1 1V20a1 1 0 0 1-1 1A17 17 0 0 1 3 4a1 1 0 0 1 1-1h3.5a1 1 0 0 1 1 1c0 1.25.2 2.45.57 3.57a1 1 0 0 1-.25 1z" fill="var(--accent)"/>
        </svg>
        (000) 000 0000
      </li>
      <li class="contact__item">
        <svg class="contact__icon" viewBox="0 0 24 24" aria-hidden="true">
          <g fill="none" stroke="var(--accent)" stroke-width="1.8">
            <circle cx="12" cy="12" r="9.5"/>
            <ellipse cx="12" cy="12" rx="4.5" ry="9.5"/>
            <line x1="2.5" y1="12" x2="21.5" y2="12"/>
            <line x1="4" y1="7" x2="20" y2="7"/>
            <line x1="4" y1="17" x2="20" y2="17"/>
          </g>
        </svg>
        www.company.com
      </li>
    </ul>
  </section>

  <section class="card card--back" aria-label="Card back">
    <div class="brand">
      <span class="brand__mark"></span>
      <span class="brand__name">Summitcrest Build Co.</span>
    </div>
  </section>

</main>
</body>
</html>
```